Start-up braucht modernes/hochwertiges Getränkeetikett
Zielgruppe
Wir sind ein modernes, nachhaltiges Start-up, welches eine neue Getränkekategorie auf den Markt bringt. Ein sogenanntes Elektrolyt-Getränk mit dem Namen FLUXO4. Es ist abgefüllt in eine 500 ml Flasche und enthält Magnesium, Kalzium, Kalium, und Natrium. Diese Stoffe (Elektrolyte) dienen der körperlichen Hydrierung. Zu Dehydrierung kann es durch Hitze, Alkohol, Sport oder Krankheit kommen. Krankheit liegt bei uns allerdings nicht im Fokus. In unserer Zielgruppe befinden sich hauptsächlich Personen im Alter von 18 - 29 Jahren.
Die Geschmacksrichtung ist Zitrone-Limette.
Aufgabenstellung
Das Etikett soll:
- MODERN, SCHLICHT und HOCHWERTIG sein, so dass es im Supermarkt hervorsticht
- erkenntlich machen, dass die Stoffe Magnesium, Natrium, Kalzium und Kalium enthalten sind
- sich farblich deutlich von der Farbe des Inhalts (weiß) abheben. (Vorzugsweise mit einem hellen Blau, türkis)
- für unsere junge Zielgruppe ansprechend sein
- ebenfalls auf die Geschmacksrichtung (Zitrone-Limette) hinweisen, und zwar so, dass wenn man eine weitere Geschmacksrichtung auf den Markt bringen möchte, diese leicht angepasst werden kann.
- nicht nach einem Energydrink oder einem typischen Sportgetränk aussehen
- unter dem Namen den Slogan 'Elektrolyt-Getränk' stehen haben
-Das Etikett ist nicht dursichtig sondern besteht aus Papier
Der Name sowie das Logo können selbstverständlich farblich verändert werden. Bei dem Logo können auch größere Änderungen vollzogen werden.
Bitte beachten Sie die unten zu stehenden Regler um sich einen guten Überblick über unsere Vorstellungen zu verschaffen. Die Platzierung des EAN-Code ist für ihr Design irrelevat .
Bei Unklarheiten gerne nachfragen!

```html
<!DOCTYPE html>
<html lang="de">
<head>
<meta charset="utf-8">
<title>FLUXO4 Elektrolyt-Getränk – Etikett</title>
<link rel="stylesheet" href="https://fonts.googleapis.com/css2?family=Comfortaa:wght@400;700&display=swap">
<style>
  :root {
    --stage: #dcdde0;
    --band-top: #8cbfe0;
    --band-blue-light: #9ccbe6;
    --band-blue-deep: #1f86c0;
    --text-white: #ffffff;
    --fill-lime: #dfe9c4;
    --fill-mint: #a9d3b4;
    --fill-teal: #3fae9c;
    --fill-deep: #2b5a52;
    --fill-dark: #203631;
  }
  * { box-sizing: border-box; margin: 0; padding: 0; }
  html, body {
    width: 667px;
    height: 1200px;
    overflow: hidden;
    background: var(--stage);
  }
  .label {
    position: absolute;
    left: 0;
    top: 81px;
    width: 667px;
    height: 1037px;
    font-family: "Comfortaa", sans-serif;
    color: var(--text-white);
    display: flex;
    flex-direction: column;
  }
  .flavour-band {
    height: 51px;
    background: var(--band-top);
    display: flex;
    align-items: center;
    justify-content: center;
    font-size: 18px;
    letter-spacing: 0.1px;
  }
  .hero {
    position: relative;
    height: 845px;
    overflow: hidden;
  }
  .hero-artwork {
    position: absolute;
    inset: 0;
    background:
      radial-gradient(ellipse 260px 300px at 42% 42%, var(--fill-lime) 0%, rgba(223,233,196,0) 100%),
      radial-gradient(ellipse 240px 340px at 78% 45%, var(--fill-teal) 0%, rgba(63,174,156,0) 100%),
      radial-gradient(ellipse 420px 260px at 40% 100%, var(--fill-dark) 0%, rgba(32,54,49,0) 100%),
      linear-gradient(160deg, var(--fill-mint) 0%, #7fbfa6 45%, var(--fill-deep) 100%);
  }
  .brand {
    position: absolute;
    right: 77px;
    top: 500px;
    text-align: right;
  }
  .brand-name {
    font-weight: 700;
    font-size: 122px;
    line-height: 1;
    letter-spacing: -2px;
  }
  .brand-claim {
    font-weight: 400;
    font-size: 30px;
    margin-top: 10px;
  }
  .minerals-band {
    flex: 1;
    background: linear-gradient(90deg, var(--band-blue-light) 0%, #5aa9d6 45%, var(--band-blue-deep) 75%, #6fb0d8 100%);
    display: flex;
    align-items: center;
    justify-content: center;
    font-size: 23px;
    font-weight: 400;
    gap: 9px;
    padding-bottom: 4px;
  }
  .minerals-band b { font-weight: 700; }
</style>
</head>
<body>
  <main class="label">
    <div class="flavour-band">Dein wachmacher in Zitrone-Limette geschmack</div>
    <section class="hero">
      <div class="hero-artwork" role="img" aria-label="Nahaufnahme grüner und türkiser Flüssigkeitsblasen mit kleinen Luftperlen"></div>
      <div class="brand">
        <div class="brand-name">FLUXO4</div>
        <div class="brand-claim">Elektrolyt-Getränk</div>
      </div>
    </section>
    <div class="minerals-band">
      <span><b>Mag</b>nesium</span>
      <span><b>Na</b>trium</span>
      <span><b>Ca</b>lcium</span>
      <span><b>K</b>alium</span>
    </div>
  </main>
</body>
</html>
```